Employee Benefits and Insurance Consulting

We are an existing company with over 30 years experience but are changing our name. We would like a simple design with grey tones.

Industry/Entity Type

Insurance

Contact Information for Business Card

Marlow Benefits Consulting
Gerald P Hollins CEO
5172 Brackenridge Road
Ridgeford, TN 37990
gerald@marlowbenefits-example.com
865-412-5593 - O
865-247-3861 - C

```html
<!DOCTYPE html>
<html lang="en">
<head>
<meta charset="utf-8">
<title>Marlow Benefits Consulting – Business Card</title>
<link href="https://fonts.googleapis.com/css2?family=Source+Sans+3:wght@400;600&display=swap" rel="stylesheet">
<style>
  :root {
    --teal: #1e9189;
    --ink: #2b2b2b;
    --grey: #6b6b6b;
    --card: #ffffff;
    --backdrop: #e6e6e4;
  }
  html, body {
    margin: 0;
    width: 1200px;
    height: 900px;
    overflow: hidden;
    background: var(--backdrop);
    font-family: "Source Sans 3", "Myriad Pro", sans-serif;
  }
  .canvas { position: relative; width: 1200px; height: 900px; }

  .card {
    position: absolute;
    background: var(--card);
    border-radius: 16px;
    box-shadow: 0 6px 18px rgba(0,0,0,0.12);
    overflow: hidden;
  }
  .card--front { left: 78px; top: 35px; width: 588px; height: 363px; }
  .card--back  { left: 389px; top: 506px; width: 566px; height: 350px; }

  .brand-band {
    position: absolute;
    left: 65px; top: 0;
    width: 137px; height: 100%;
    background: var(--teal);
  }
  .brand-band__name {
    position: absolute;
    left: 50%; top: 50%;
    transform: translate(-50%, -50%) rotate(-90deg);
    white-space: nowrap;
    text-align: center;
    color: #ffffff;
    font-weight: 600;
    line-height: 1.15;
    letter-spacing: 1px;
  }
  .brand-band__name .line-main { display: block; font-size: 29px; }
  .brand-band__name .line-sub  { display: block; font-size: 15px; letter-spacing: 5px; }

  .contact { position: absolute; left: 284px; top: 92px; color: var(--ink); }
  .contact__name {
    margin: 0;
    color: var(--teal);
    font-size: 22px;
    font-weight: 600;
  }
  .contact__role { font-size: 16px; }
  .contact__address {
    margin: 24px 0 0;
    font-style: normal;
    font-size: 16px;
    line-height: 22px;
  }
  .contact__list { list-style: none; margin: 20px 0 0; padding: 0; font-size: 16px; }
  .contact__list li { display: flex; align-items: center; height: 24.5px; }
  .contact__list svg { width: 12px; height: 12px; margin-right: 12px; flex: none; fill: var(--teal); }
  .contact__list .email { font-size: 15px; }

  .wordmark {
    position: absolute;
    left: 0; right: 0; top: 196px;
    display: flex; align-items: center; justify-content: center; gap: 12px;
    color: var(--teal);
    font-weight: 600;
    font-size: 28px;
    letter-spacing: 1px;
  }
  .wordmark__square { width: 18px; height: 18px; background: var(--grey); }
</style>
</head>
<body>
<main class="canvas">

  <section class="card card--front" aria-label="Business card front">
    <div class="brand-band">
      <div class="brand-band__name">
        <span class="line-main">MARLOW BENEFITS</span>
        <span class="line-sub">CONSULTING</span>
      </div>
    </div>
    <div class="contact">
      <h1 class="contact__name">Gerald P Hollins <span class="contact__role">- CEO</span></h1>
      <address class="contact__address">5172 Brackenridge Road<br>Ridgeford, TN 37990</address>
      <ul class="contact__list">
        <li>
          <svg viewBox="0 0 12 12" aria-hidden="true"><path d="M2.4 0.5 4.2 2.8 3.3 4.2C4 5.9 6 7.9 7.8 8.7L9.2 7.8 11.5 9.6 10.4 11.5C5 11.3 0.7 7 0.5 1.6Z"/></svg>
          865-247-3861
        </li>
        <li>
          <svg viewBox="0 0 12 12" aria-hidden="true"><path d="M3 0h6a1 1 0 0 1 1 1v10a1 1 0 0 1-1 1H3a1 1 0 0 1-1-1V1a1 1 0 0 1 1-1Zm0.8 1.5v7.5h4.4V1.5Z"/></svg>
          865-412-5593
        </li>
        <li>
          <svg viewBox="0 0 12 12" aria-hidden="true"><path d="M0 2.5h12v7H0Zm1 0.8v0.3l5 3.2 5-3.2v-0.3Z"/></svg>
          <span class="email">gerald@marlowbenefits-example.com</span>
        </li>
      </ul>
    </div>
  </section>

  <section class="card card--back" aria-label="Business card back">
    <div class="wordmark">
      <span class="wordmark__square" aria-hidden="true"></span>
      <span>MARLOW BENEFITS CONSULTING</span>
    </div>
  </section>

</main>
</body>
</html>
```